Wordpress Site Design for a Horror and Action Movie Production Company

We need a re-design/facelift of our website: https://k42t.pagecraft.io
The structure of the website could remain the same, but it needs to look and feel BETTER!

We would like the website coded in Wordpress so that it can be easily updated bu us, via adding new projects and new projects' info.

We specialize in Action, Horror, and Sci-Fi Genre. That being said, we don't want the website to look like it's a themed park with haunted houses. It should still be sharp and professional, as after all - it is a business for us!

Target Market(s)

Film Distribution Companies (B2B), as well as general audience that likes movies

Industry/Entity Type

Movie Production

Coding

Coded - Design and coding required

Number of Pages Required

5+ page

Font styles to use
Sans Serif

Colors

Designer to choose colors to be used in the design.

Requirements
Must have
• - PROJECTS page
• - Each PROJECT has a sub-page with project info/updates (up dates could be in a form of a WP post, ideally a template that we can use to update and create new PROJECT pages, with text, poster, and video link (trailer))
• - NEWS page that chronologically lists updates from all PROJECTS (could be done via WP blog)
• - HOME page would
Nice to have
• Should generally have a dark background.
• Websites we like as a reference of general approach and style:
• https://marbletoq.com
• https://velunpix.com (however this is very image-centric, and we might not have that much imagery at the moment)
• https://www.copperfieldechoandframe.com/other
• https://quennreels.com
Should not have
• We specialize in Action, Horror, and Sci-Fi Genre. That being said, we don't want the website to look like it's a themed park with haunted houses. It should still be sharp and professional, as after all - it is a business for us!

```html
<!DOCTYPE html>
<html lang="en">
<head>
<meta charset="utf-8">
<title>Vault 27 Pictures</title>
<link href="https://fonts.googleapis.com/css2?family=Montserrat:wght@300;400;600;700;800&family=Lato:wght@400;700&display=swap" rel="stylesheet">
<style>
:root{
  --gold:#f2c511;
  --gold-soft:#f7d955;
  --ink:#15110e;
  --ink-2:#1f1915;
  --brown:#4a3520;
  --text:#e9e3da;
  --muted:#bfb6a9;
  --white:#ffffff;
}
*{margin:0;padding:0;box-sizing:border-box}
html,body{width:1200px;height:4819px;overflow:hidden;background:var(--ink)}
body{font-family:"Lato",sans-serif;color:var(--text)}
.page{position:relative;width:1200px;height:4819px;overflow:hidden;
  background:
   radial-gradient(ellipse 520px 420px at 900px 1450px,rgba(120,85,45,.35),transparent 70%),
   radial-gradient(ellipse 600px 500px at 300px 2450px,rgba(140,100,55,.35),transparent 70%),
   radial-gradient(ellipse 500px 400px at 250px 3250px,rgba(110,80,45,.3),transparent 70%),
   linear-gradient(180deg,#1a1511 0%,#120f0c 40%,#1b1612 70%,#14100d 100%);}
.abs{position:absolute}
.heading{font-family:"Montserrat",sans-serif;color:var(--white);font-size:38px;letter-spacing:.5px}
.heading b{font-weight:800}
.heading span{font-weight:400}
.rule{display:inline-block;width:54px;height:2px;background:var(--gold);vertical-align:middle;margin-left:24px}
.btn{position:absolute;background:var(--gold);color:var(--white);font-family:"Montserrat",sans-serif;font-weight:700;font-size:15px;border-radius:22px;display:flex;align-items:center;justify-content:center;gap:8px;text-transform:uppercase}

/* header */
.site-header{left:0;top:0;width:1200px;height:103px;background:var(--white)}
.brand{left:112px;top:30px;font-family:"Montserrat",sans-serif;font-weight:700;font-size:30px;color:#1b1b1b;letter-spacing:1px}
.nav{left:627px;top:61px;font-family:"Montserrat",sans-serif;font-size:15px;font-weight:600;color:#222}
.nav a{position:absolute;white-space:nowrap;color:#222;text-decoration:none}
.nav .active{color:var(--gold)}
.nav .active:before{content:"";position:absolute;left:-6px;top:-12px;width:60px;height:6px;border-top:3px solid var(--gold);border-radius:50% 50% 0 0}
.search{left:964px;top:17px;width:122px;height:27px;background:var(--gold);color:var(--white);border-radius:14px;font-family:"Montserrat",sans-serif;font-weight:700;font-size:13px;display:flex;align-items:center;justify-content:center;gap:6px}

/* hero */
.hero{left:0;top:103px;width:1200px;height:700px;
  background:radial-gradient(ellipse 420px 380px at 300px 220px,#6b5435 0%,#3a2c1c 45%,transparent 80%),
  radial-gradient(ellipse 300px 260px at 620px 300px,rgba(120,95,60,.5),transparent 75%),
  linear-gradient(180deg,#221a12,#120e0b)}
.hero-title{left:0;top:208px;width:1200px;text-align:center;font-family:"Montserrat",sans-serif;color:var(--white);font-weight:700;font-size:52px;line-height:60px}
.hero-sub{left:0;top:280px;width:1200px;text-align:center;font-family:"Montserrat",sans-serif;color:var(--white);font-weight:300;font-size:54px;letter-spacing:2px}
.hero-text{left:280px;top:356px;width:640px;text-align:center;font-size:16px;line-height:26px;color:var(--text)}
.dots{left:567px;top:562px;display:flex;gap:5px}
.dots i{width:13px;height:13px;border:2px solid var(--gold);border-radius:50%}
.dots i.on{background:var(--gold)}

/* about */
.about-photo{left:112px;top:818px;width:428px;height:428px;border-radius:50%;
  background:radial-gradient(circle at 60% 35%,#d9a066 0%,#a4612b 35%,#4e2a12 75%,#2a170b 100%)}
.about-title{left:599px;top:860px}
.about-sub{left:599px;top:937px;font-family:"Montserrat",sans-serif;font-weight:700;font-size:27px;color:var(--gold)}
.about-text{left:599px;top:973px;width:489px;font-size:15.5px;line-height:30px;text-align:justify;color:var(--text)}

/* projects */
.projects-title{left:450px;top:1466px}
.project{position:absolute;width:277px}
.project .frame{position:absolute;left:4px;top:-17px;width:250px;height:170px;border-top:12px solid var(--gold);border-left:18px solid var(--gold)}
.project .poster{position:absolute;left:22px;top:0;width:255px;height:176px}
.project h3{position:absolute;left:0;top:196px;width:277px;font-family:"Montserrat",sans-serif;font-weight:600;font-size:19px;color:var(--gold);padding-bottom:8px;border-bottom:3px solid var(--gold)}
.project p{position:absolute;left:0;top:247px;width:277px;font-size:14px;line-height:23.5px;text-align:justify;color:var(--text)}
.project .more{position:absolute;left:0;top:360px;font-family:"Montserrat",sans-serif;font-size:16px;color:var(--white);display:flex;align-items:center;gap:6px}
.arrow{position:absolute;color:var(--gold)}

/* works */
.works-title{left:440px;top:2342px}
.tile{position:absolute}
.tile-caption{position:absolute;left:56px;top:78px;font-family:"Montserrat",sans-serif;color:var(--white)}
.tile-caption h4{font-weight:700;font-size:18px;margin-bottom:10px}
.tile-caption p{font-family:"Lato",sans-serif;font-size:15px;line-height:26px;width:420px}

/* subscribe */
.subscribe{left:0;top:3465px;width:1200px;height:397px;background:var(--gold)}
.subscribe-title{left:0;top:3538px;width:1200px;text-align:center;font-family:"Montserrat",sans-serif;font-weight:800;font-size:38px;color:var(--white)}
.subscribe-title .rule{background:var(--white)}
.subscribe-sub{left:0;top:3605px;width:1200px;text-align:center;font-size:15px;color:var(--white)}
.sub-input{left:425px;top:3654px;width:333px;height:47px;background:var(--gold-soft);color:var(--white);font-size:12px;display:flex;align-items:center;justify-content:center}
.sub-btn{left:509px;top:3735px;width:165px;height:41px;border:2px solid var(--white);color:var(--white);font-family:"Montserrat",sans-serif;font-weight:700;font-size:14px;display:flex;align-items:center;justify-content:center}

/* partners */
.partners-bg{left:0;top:3862px;width:1200px;height:957px;
  background:radial-gradient(ellipse 500px 300px at 300px 120px,rgba(120,95,60,.45),transparent 75%),
  radial-gradient(ellipse 400px 260px at 950px 100px,rgba(110,90,60,.4),transparent 75%),
  linear-gradient(180deg,#2a2119,#16120e 55%,#120e0b)}
.partners-title{left:0;top:3945px;width:1200px;text-align:center;font-family:"Montserrat",sans-serif;font-weight:800;font-size:38px;color:var(--white)}
.partner{position:absolute;top:4072px;height:164px;background:linear-gradient(135deg,#8a8a8a,#3b3b3b 60%,#1e1e1e)}
.partner-name{position:absolute;left:0;top:74px;width:100%;text-align:center;font-family:"Montserrat",sans-serif;font-weight:700;font-size:14px;color:var(--white)}

/* contact */
.contact-title{left:0;top:4362px;width:1200px;text-align:center;font-family:"Montserrat",sans-serif;font-weight:700;font-size:23px;color:var(--white)}
.field{position:absolute;border:2px solid var(--white);border-radius:6px;font-size:14px;color:var(--white);padding:8px 16px}
.contact-btn{left:281px;top:4624px;width:108px;height:28px;font-size:13px;font-weight:400;border-radius:14px}
.info{position:absolute;top:4697px;font-size:14px;line-height:26px;color:var(--white);display:flex;gap:12px;align-items:flex-start}
.copyright{left:0;top:4785px;width:1200px;text-align:center;font-size:14px;color:var(--white)}
</style>
</head>
<body>
<div class="page">

  <header class="abs site-header">
    <div class="abs brand">VAULT 27 PICTURES</div>
    <nav class="abs nav">
      <a class="active" style="left:0">Home</a>
      <a style="left:113px">About us</a>
      <a style="left:247px">Projects</a>
      <a style="left:374px">Contact Us</a>
    </nav>
    <div class="abs search">
      <svg width="13" height="13" viewBox="0 0 14 14"><circle cx="6" cy="6" r="4.5" fill="none" stroke="#fff" stroke-width="2"/><path d="M9.5 9.5 13 13" stroke="#fff" stroke-width="2"/></svg>
      SEARCH
    </div>
  </header>

  <section class="abs hero" role="img" aria-label="Vintage film projector in warm light on a dark background"></section>
  <h1 class="abs hero-title">VAULT 27</h1>
  <div class="abs hero-sub">PICTURES</div>
  <p class="abs hero-text">The decades of combined experience of the 4 founders of Vault 27 Pictures provide an unparalleled expertise of storytelling, production</p>
  <div class="btn" style="left:470px;top:442px;width:122px;height:39px;font-size:14px">Read More</div>
  <div class="btn" style="left:608px;top:442px;width:141px;height:39px;font-size:14px">Contact Us</div>
  <div class="abs dots"><i></i><i></i><i class="on"></i><i></i></div>

  <svg class="abs" style="left:0;top:0" width="1200" height="2400" viewBox="0 0 1200 2400">
    <path d="M0 767 Q600 487 1200 767 Q600 553 0 767Z" fill="#f2c511"/>
    <path d="M0 2100 Q600 2374 1200 2100 Q600 2280 0 2100Z" fill="#f2c511"/>
  </svg>

  <div class="abs about-photo" role="img" aria-label="Close-up of a film camera with a monitor on set"></div>
  <svg class="abs" style="left:112px;top:818px" width="445" height="430" viewBox="0 0 445 430">
    <path d="M214 1 A214 214 0 0 1 214 429 A204 214 0 0 0 214 1Z" fill="#f2c511" transform="translate(6 0)"/>
  </svg>
  <h2 class="abs heading about-title"><b>ABOUT</b><span> US</span><i class="rule"></i></h2>
  <div class="abs about-sub">Vault 27 Pictures</div>
  <p class="abs about-text">We produce genre feature films, series, documentaries, and anything else that we feel great about. We take pride in our innovative approach to the process of filmmaking and marketing of our produced content.</p>
  <div class="btn" style="left:599px;top:1133px;width:155px;height:43px">Read More
    <svg width="14" height="14" viewBox="0 0 14 14"><circle cx="7" cy="7" r="7" fill="#fff"/><path d="M5.5 4 8.5 7 5.5 10" stroke="#f2c511" stroke-width="2" fill="none"/></svg>
  </div>

  <h2 class="abs heading projects-title"><b>OUR</b><span> PROJECTS</span><i class="rule" style="width:54px;margin-left:50px"></i></h2>
  <svg class="arrow" style="left:72px;top:1705px" width="14" height="22" viewBox="0 0 14 22"><path d="M11 2 3 11 11 20" stroke="#f2c511" stroke-width="3" fill="none"/></svg>
  <svg class="arrow" style="left:1110px;top:1705px" width="14" height="22" viewBox="0 0 14 22"><path d="M3 2 11 11 3 20" stroke="#f2c511" stroke-width="3" fill="none"/></svg>

  <article class="project" style="left:115px;top:1606px;height:400px">
    <div class="frame"></div>
    <div class="poster" role="img" aria-label="Northlight film poster" style="background:linear-gradient(135deg,#1b1b1b,#6a3a30 45%,#c9c0b8 75%,#222)"></div>
    <h3>NORTHLIGHT</h3>
    <p>Lorem ipsum dolor sit amet, consectetur adipiscing elit, sed do eiusmod tempor incididunt ut labore et dolore magna aliqua. Quis ipsum suspendisse</p>
    <div class="more">READ MORE <svg width="14" height="14" viewBox="0 0 14 14"><circle cx="7" cy="7" r="7" fill="#f2c511"/><path d="M5.5 4 8.5 7 5.5 10" stroke="#fff" stroke-width="2" fill="none"/></svg></div>
  </article>

  <article class="project" style="left:462px;top:1664px;height:400px">
    <div class="frame"></div>
    <div class="poster" role="img" aria-label="Dark Tide film poster" style="background:linear-gradient(135deg,#0d0d0d,#3a2a26 45%,#8a7f78 70%,#2a1414)"></div>
    <h3>DARK TIDE</h3>
    <p>Lorem ipsum dolor sit amet, consectetur adipiscing elit, sed do eiusmod tempor incididunt ut labore et dolore magna aliqua. Quis ipsum suspendisse</p>
    <div class="more">READ MORE <svg width="14" height="14" viewBox="0 0 14 14"><circle cx="7" cy="7" r="7" fill="#f2c511"/><path d="M5.5 4 8.5 7 5.5 10" stroke="#fff" stroke-width="2" fill="none"/></svg></div>
  </article>

  <article class="project" style="left:811px;top:1606px;height:400px">
    <div class="frame"></div>
    <div class="poster" role="img" aria-label="Neon Rider film poster" style="background:linear-gradient(180deg,#0a0a0a 30%,#4c5566 70%,#9aa0a8)"></div>
    <h3>NEON RIDER</h3>
    <p>Lorem ipsum dolor sit amet, consectetur adipiscing elit, sed do eiusmod tempor incididunt ut labore et dolore magna aliqua. Quis ipsum suspendisse</p>
    <div class="more">READ MORE <svg width="14" height="14" viewBox="0 0 14 14"><circle cx="7" cy="7" r="7" fill="#f2c511"/><path d="M5.5 4 8.5 7 5.5 10" stroke="#fff" stroke-width="2" fill="none"/></svg></div>
  </article>

  <h2 class="abs heading works-title"><b>OUR WORKS</b><i class="rule" style="margin-left:26px"></i></h2>
  <div class="tile" role="img" aria-label="Film still: heroine on railway tracks with helicopters above" style="left:168px;top:2521px;width:276px;height:259px;background:linear-gradient(135deg,#6a5a48,#3a2f26 50%,#1c1814)"></div>
  <div class="tile" role="img" aria-label="Film still: army marching through smoke" style="left:462px;top:2473px;width:276px;height:260px;background:linear-gradient(180deg,#6b6a66,#3a3936 55%,#1c1b1a)"></div>
  <div class="tile" role="img" aria-label="Film still: hand rising from a graveyard" style="left:758px;top:2574px;width:275px;height:159px;background:linear-gradient(180deg,#5c7488,#2b3a46 60%,#141a20)"></div>
  <div class="tile" role="img" aria-label="Film still: armed soldier in front of ruined houses" style="left:110px;top:2802px;width:334px;height:410px;background:linear-gradient(180deg,#5a4e44,#3a2f27 45%,#1a1512)"></div>
  <div class="tile" role="img" aria-label="Film still: spaceships over a ruined city" style="left:462px;top:2752px;width:628px;height:254px;background:linear-gradient(135deg,#6a5f2a,#4a4020 50%,#2a2412)">
    <div class="tile-caption">
      <h4>VAULT 27 PICTURES</h4>
      <p>Reel Ledger: Crowline Films partners on production arm, Vault 27 Pictures</p>
    </div>
  </div>
  <div class="tile" role="img" aria-label="Film still: soldier firing in battle" style="left:466px;top:3031px;width:272px;height:254px;background:linear-gradient(135deg,#1a1a18,#7a6a3a 50%,#c8a040 70%,#2a2218)"></div>
  <div class="tile" role="img" aria-label="Film still: group of armed women, black and white" style="left:758px;top:3031px;width:272px;height:148px;background:linear-gradient(180deg,#7a7a7a,#3a3a3a 60%,#1a1a1a)"></div>

  <section class="abs subscribe"></section>
  <h2 class="abs subscribe-title">SUBSCRIBE<i class="rule" style="width:52px"></i></h2>
  <div class="abs subscribe-sub">Vault 27 Pictures</div>
  <div class="abs sub-input">YOUR EMAIL</div>
  <div class="abs sub-btn">SUBMIT</div>

  <section class="abs partners-bg" role="img" aria-label="Vintage film equipment in sepia tones"></section>
  <h2 class="abs partners-title">PARTNERS</h2>
  <svg class="arrow" style="left:72px;top:4143px" width="14" height="22" viewBox="0 0 14 22"><path d="M11 2 3 11 11 20" stroke="#f2c511" stroke-width="3" fill="none"/></svg>
  <svg class="arrow" style="left:1110px;top:4143px" width="14" height="22" viewBox="0 0 14 22"><path d="M3 2 11 11 3 20" stroke="#f2c511" stroke-width="3" fill="none"/></svg>
  <div class="partner" role="img" aria-label="Black and white portrait of a partner" style="left:112px;width:324px"></div>
  <div class="partner" role="img" aria-label="Darkened portrait of partner Renzo Valkar" style="left:462px;width:296px;background:linear-gradient(135deg,#3a3a3a,#1e1e1e)"><div class="partner-name">RENZO VALKAR</div></div>
  <div class="partner" role="img" aria-label="Black and white portrait of a partner" style="left:760px;width:328px"></div>

  <h2 class="abs contact-title">CONTACT INFORMATION</h2>
  <div class="field" style="left:273px;top:4435px;width:311px;height:33px">Name</div>
  <div class="field" style="left:593px;top:4435px;width:311px;height:33px">Last name</div>
  <div class="field" style="left:273px;top:4482px;width:311px;height:33px">Phone</div>
  <div class="field" style="left:593px;top:4482px;width:311px;height:33px">City</div>
  <div class="field" style="left:273px;top:4528px;width:631px;height:73px">Message</div>
  <div class="btn contact-btn">SUBMIT</div>

  <div class="info" style="left:243px">
    <svg width="18" height="26" viewBox="0 0 18 26"><path d="M9 1C4.6 1 1 4.6 1 9c0 6 8 16 8 16s8-10 8-16c0-4.4-3.6-8-8-8z" fill="none" stroke="#fff" stroke-width="1.6"/><circle cx="9" cy="9" r="3" fill="none" stroke="#fff" stroke-width="1.6"/></svg>
    <div>418 P.O. Box<br>Cedar Hollow Oregon 97120</div>
  </div>
  <div class="info" style="left:543px">
    <svg width="22" height="16" viewBox="0 0 22 16" style="margin-top:4px"><rect x="1" y="1" width="20" height="14" fill="none" stroke="#fff" stroke-width="1.6"/><path d="M1 1 11 9 21 1" fill="none" stroke="#fff" stroke-width="1.6"/></svg>
    <div style="margin-left:10px">info@vault27pictures.com</div>
  </div>
  <div class="info" style="left:801px">
    <svg width="22" height="22" viewBox="0 0 22 22" style="margin-top:3px"><circle cx="11" cy="11" r="10" fill="none" stroke="#fff" stroke-width="1.6"/><path d="M7 6c0 5 4 9 9 9l1-2-3-1-1 1c-2-1-3-2-4-4l1-1-1-3z" fill="#fff"/></svg>
    <div style="margin-left:-4px;margin-top:3px">(555) 210-4478</div>
  </div>

  <div class="abs copyright">Copyright @ 2019 All right reserved</div>
</div>
</body>
</html>
```